Keystone Trench Co Business Card*

Looking for a professional, clean and crisp business card

I am in the underground utilities industry and am just looking for a really impressive business card. I would like our card to be white with our symbol crisp and clear with it protruding. I also have a business partner that will require his name and info on the card once the design is set. I would like to have our website info on the card which is;
http://keystonetrenchco.example/

Contact Information for Business Card

Website, contact name, number and email

```html
<!DOCTYPE html>
<html lang="en">
<head>
<meta charset="utf-8">
<title>Keystone Trench Co — Business Card</title>
<link rel="stylesheet" href="https://fonts.googleapis.com/css2?family=Bebas+Neue&family=Arimo:wght@400&display=swap">
<style>
  :root {
    --stage: #2b2b2d;
    --card-white: #ffffff;
    --card-black: #17181a;
    --ink: #161616;
    --brand-blue: #3a62b0;
    --rule: #222222;
  }
  * { margin: 0; padding: 0; box-sizing: border-box; }
  html, body { width: 1200px; height: 1108px; overflow: hidden; }
  body { background: var(--stage); position: relative; font-family: "Arimo", Arial, sans-serif; }

  .card {
    position: absolute;
    width: 440px;
    height: 720px;
    border-radius: 26px;
  }
  .card--front {
    left: 130px; top: 170px;
    background: var(--card-white);
    display: flex; flex-direction: column; align-items: center;
  }
  .card--back {
    left: 630px; top: 220px;
    background: var(--card-black);
    overflow: hidden;
  }

  .brand-mark {
    margin-top: 150px;
    display: flex; align-items: center; gap: 14px;
  }
  .brand-mark__dot {
    width: 34px; height: 34px; border-radius: 50%;
    background: var(--ink);
  }
  .brand-mark__name {
    font-family: "Bebas Neue", Arial, sans-serif;
    font-size: 50px; line-height: 1;
    color: var(--ink);
    letter-spacing: 1px;
  }

  .person { margin-top: 190px; text-align: center; }
  .person__name {
    font-family: "Bebas Neue", Arial, sans-serif;
    font-size: 40px; line-height: 1;
    color: var(--brand-blue);
    letter-spacing: 0.5px;
  }
  .person__role { font-size: 21px; color: var(--ink); margin-top: 4px; }

  .contact-icons {
    margin-top: 24px;
    display: flex; align-items: center; gap: 8px;
  }
  .contact-icons__rule { width: 52px; height: 1px; background: var(--rule); margin: 0 6px; }
  .contact-icons__tile {
    width: 34px; height: 34px; border-radius: 5px;
    background: var(--brand-blue);
    display: flex; align-items: center; justify-content: center;
  }

  .contact-list { margin-top: 20px; text-align: center; font-size: 21px; line-height: 1.35; color: var(--ink); }

  .back-pattern {
    position: absolute; inset: 0;
    background: radial-gradient(circle at 50% 45%, #202124 0%, #17181a 75%);
  }
  .back-mark {
    position: absolute; left: 0; right: 0; top: 560px;
    display: flex; align-items: center; justify-content: center; gap: 10px;
  }
  .back-mark__dot { width: 20px; height: 20px; border-radius: 50%; background: #ffffff; }
  .back-mark__name {
    font-family: "Bebas Neue", Arial, sans-serif;
    font-size: 30px; line-height: 1; color: #ffffff; letter-spacing: 0.5px;
  }
</style>
</head>
<body>
  <section class="card card--front" aria-label="Card front">
    <div class="brand-mark">
      <span class="brand-mark__dot"></span>
      <span class="brand-mark__name">Keystone Trench Co</span>
    </div>

    <div class="person">
      <h1 class="person__name">Marcus Hale</h1>
      <p class="person__role">Managing Director</p>
    </div>

    <div class="contact-icons">
      <span class="contact-icons__rule"></span>
      <span class="contact-icons__tile">
        <svg width="20" height="20" viewBox="0 0 24 24" aria-label="Phone"><path fill="#fff" d="M6.6 10.8a15 15 0 0 0 6.6 6.6l2.2-2.2a1 1 0 0 1 1-.25 11.4 11.4 0 0 0 3.6.57 1 1 0 0 1 1 1V20a1 1 0 0 1-1 1A17 17 0 0 1 3 4a1 1 0 0 1 1-1h3.5a1 1 0 0 1 1 1c0 1.25.2 2.45.57 3.57a1 1 0 0 1-.25 1z"/></svg>
      </span>
      <span class="contact-icons__tile">
        <svg width="20" height="20" viewBox="0 0 24 24" aria-label="Email"><rect x="2.5" y="5" width="19" height="14" rx="1" fill="none" stroke="#fff" stroke-width="2"/><path d="M3 6l9 7 9-7" fill="none" stroke="#fff" stroke-width="2"/></svg>
      </span>
      <span class="contact-icons__tile">
        <svg width="20" height="20" viewBox="0 0 24 24" aria-label="Website"><circle cx="12" cy="12" r="9" fill="none" stroke="#fff" stroke-width="2"/><path d="M3 12h18M12 3c3 3 3 15 0 18M12 3c-3 3-3 15 0 18" fill="none" stroke="#fff" stroke-width="1.5"/></svg>
      </span>
      <span class="contact-icons__rule"></span>
    </div>

    <ul class="contact-list" style="list-style:none">
      <li>044-555 019 274</li>
      <li>hello@keystonetrenchco.example</li>
      <li>www.keystonetrenchco.example</li>
    </ul>
  </section>

  <section class="card card--back" aria-label="Card back">
    <div class="back-pattern" role="img" aria-label="Faint repeating brand pattern on dark background"></div>
    <div class="back-mark">
      <span class="back-mark__dot"></span>
      <span class="back-mark__name">Keystone Trench Co</span>
    </div>
  </section>
</body>
</html>
```